Company Profile for Academic and Study Abroad Services

I am looking for Power Point Design for company Profile . the company is academic and study abroad services. you can visit the website which is www.korvapath.ae . the colour i prefer is Dark Blue + White + Black . you can find all the content for power point and logo and some picture i need you to add it.

Target Market(s)

Students who wants to study abroad. Universities . Learning centre.

Industry/Entity Type

Education

Font styles to use
Serif
Sans Serif

Colors
0555a3
ffffff
000000
aaaaaa

Requirements
Must have
• Must Have Images for each slides.
Nice to have
• infographic. Images related to the study abroad

```html
<!DOCTYPE html>
<html lang="en">
<head>
<meta charset="utf-8">
<title>Korvapath – Company Profile Slides</title>
<link rel="stylesheet" href="https://fonts.googleapis.com/css2?family=Open+Sans:wght@400;600;700&display=swap">
<style>
  :root {
    --navy: #033d80;
    --navy-deep: #072c62;
    --ink: #333338;
    --grey-dark: #5c5c61;
    --grey-mid: #88888d;
    --grey-text: #7d7d82;
    --panel-light: #f2f2f2;
    --panel-mid: #e3e3e4;
    --rule: #e6e6e8;
    --white: #ffffff;
    --stage: #e8e8ea;
    --photo-a: #c9b7a4;
    --photo-b: #4d4a5a;
    --sky-a: #d9e6ef;
    --sky-b: #9a8a80;
    --mint: #cfeef0;
    --mist: #d8dde2;
  }
  * { box-sizing: border-box; margin: 0; padding: 0; }
  html, body { width: 1200px; height: 1200px; overflow: hidden; }
  body {
    background: var(--stage);
    font-family: "Open Sans", Arial, sans-serif;
    color: var(--ink);
    position: relative;
  }
  .slide {
    position: absolute;
    width: 414px;
    height: 288px;
    background: var(--white);
    overflow: hidden;
  }
  .slide--cover { left: 170px; top: 122px; }
  .slide--who { left: 636px; top: 118px; }
  .slide--what { left: 170px; top: 464px; }
  .slide--levels { left: 636px; top: 464px; }
  .slide--why { left: 170px; top: 808px; }
  .slide--destination { left: 636px; top: 808px; }

  .abs { position: absolute; }

  /* brand mark: name with one square */
  .brand {
    position: absolute;
    display: flex;
    align-items: center;
    gap: 4px;
    font-weight: 700;
    font-size: 8.5px;
    letter-spacing: 0.3px;
    color: var(--navy);
  }
  .brand__square { width: 8px; height: 8px; background: var(--navy); }
  .slide .brand--corner { right: 12px; top: 22px; }

  .header-band {
    position: absolute;
    left: 0; top: 0;
    height: 57px;
    background: var(--navy);
    color: var(--white);
    font-size: 15px;
    font-weight: 400;
    display: flex;
    align-items: center;
    padding-left: 34px;
    letter-spacing: 0.1px;
  }
  .slide-title {
    position: absolute;
    color: var(--navy);
    font-size: 14.5px;
    font-weight: 400;
  }
  .fine {
    font-size: 5.6px;
    line-height: 1.45;
    color: var(--ink);
  }
  .site-url {
    position: absolute;
    left: 20px;
    font-size: 9.5px;
    font-weight: 600;
    color: var(--navy);
  }
  .foot-bar {
    position: absolute;
    left: 0; bottom: 0;
    width: 100%;
    height: 11px;
    background: var(--navy-deep);
  }

  /* cover */
  .cover__photo {
    position: absolute; inset: 0;
    background: linear-gradient(160deg, #b9c48a 0%, var(--photo-a) 35%, #8a7d86 60%, var(--photo-b) 100%);
  }
  .cover__brand-box {
    position: absolute; left: 0; top: 174px;
    width: 126px; height: 56px;
    background: var(--white);
  }
  .cover__brand-box .brand { left: 34px; top: 23px; }
  .cover__bevel { position: absolute; left: 126px; top: 160px; }
  .cover__band {
    position: absolute; left: 159px; top: 174px;
    width: 255px; height: 56px;
    background: var(--navy);
    color: var(--white);
    font-weight: 700;
    font-size: 10.5px;
    line-height: 1.45;
    padding: 13px 0 0 53px;
  }

  /* who we are */
  .who__chart { position: absolute; left: 0; top: 90px; }
  .who__caption { position: absolute; left: 24px; top: 254px; width: 370px; }

  /* what we do */
  .what__icon {
    position: absolute; top: 92px;
    width: 54px; height: 54px;
    border-radius: 50%;
    background: var(--grey-dark);
    display: flex; align-items: center; justify-content: center;
  }
  .what__label {
    position: absolute; top: 169px;
    width: 138px;
    text-align: center;
    font-size: 10px;
    font-weight: 600;
    color: var(--grey-text);
  }
  .what__panel {
    position: absolute; top: 189px;
    width: 138px; height: 99px;
    background: var(--panel-light);
    padding: 30px 20px 0 22px;
  }
  .what__panel--mid { background: var(--panel-mid); }

  /* education levels */
  .levels__photo {
    position: absolute; left: 153px; top: 62px;
    width: 108px; height: 108px;
    border-radius: 50%;
    background: linear-gradient(160deg, var(--mint) 0%, #e6f1f4 50%, var(--mist) 100%);
  }
  .levels__photo-label {
    position: absolute; left: 0; right: 0; top: 48px;
    text-align: center; font-size: 9px; color: var(--white);
  }
  .levels__heading {
    position: absolute; left: 0; right: 0; top: 170px;
    text-align: center;
    font-size: 15.5px; font-weight: 600;
    color: var(--grey-text);
  }
  .levels__text {
    position: absolute; left: 64px; width: 286px; top: 198px;
    text-align: center;
  }

  /* why choose */
  .why__donut { position: absolute; left: 30px; top: 78px; }
  .why__point {
    position: absolute;
    width: 92px;
    padding-left: 8px;
  }
  .why__point::before {
    content: "";
    position: absolute; left: 0; top: 2px;
    width: 3px; height: 3px;
    background: var(--navy);
    transform: rotate(45deg);
  }
  .why__point--plain::before { background: var(--rule); }
  .why__rule {
    position: absolute; left: 266px; top: 84px;
    width: 2px; height: 108px;
    background: var(--rule);
  }
  .why__text { position: absolute; left: 297px; top: 80px; width: 110px; font-size: 6px; }

  /* study destination */
  .dest__photo {
    position: absolute; left: 8px; top: 80px;
    width: 406px; height: 82px;
    background: linear-gradient(180deg, var(--sky-a) 0%, #bccbd6 45%, var(--sky-b) 100%);
  }
  .dest__tab {
    position: absolute; top: 166px;
    width: 103.5px; height: 31px;
    background: var(--grey-dark);
    display: flex; align-items: center; justify-content: center;
  }
  .dest__tab--light { background: var(--grey-mid); }
  .dest__strip {
    position: absolute; left: 0; top: 197px;
    width: 414px; height: 72px;
    background: var(--panel-light);
  }
  .dest__col { position: absolute; top: 207px; width: 66px; }
</style>
</head>
<body>

<!-- Cover -->
<section class="slide slide--cover">
  <div class="cover__photo" role="img" aria-label="Photo of smiling graduates in caps and gowns holding diplomas"></div>
  <div class="cover__brand-box">
    <div class="brand"><span class="brand__square"></span>KORVAPATH</div>
  </div>
  <svg class="cover__bevel" width="33" height="70" viewBox="0 0 33 70" aria-hidden="true">
    <polygon points="0,14 33,0 33,70 0,70" fill="#8a8a8e"/>
    <polygon points="0,14 33,0 33,14 0,14" fill="#a3a3a7"/>
  </svg>
  <div class="cover__band">KORVAPATH<br>Universities Entrance Services</div>
</section>

<!-- Who we are -->
<section class="slide slide--who">
  <div class="header-band" style="width:327px;">WHO WE ARE</div>
  <div class="brand brand--corner"><span class="brand__square"></span>KORVAPATH</div>
  <svg class="who__chart" width="414" height="152" viewBox="0 0 414 152" aria-hidden="true">
    <g stroke="#e9e9eb" stroke-width="1">
      <line x1="0" y1="2" x2="414" y2="2"/>
      <line x1="0" y1="20" x2="414" y2="20"/>
      <line x1="0" y1="38" x2="414" y2="38"/>
      <line x1="0" y1="56" x2="414" y2="56"/>
      <line x1="0" y1="74" x2="414" y2="74"/>
      <line x1="0" y1="92" x2="414" y2="92"/>
      <line x1="0" y1="110" x2="414" y2="110"/>
      <line x1="0" y1="128" x2="414" y2="128"/>
      <line x1="0" y1="150" x2="414" y2="150"/>
    </g>
    <rect x="31" y="32" width="4" height="118" fill="#6d6d71"/>
    <polygon points="46,150 110,38 170,150" fill="#5f5f63"/>
    <polygon points="212,150 300,75 390,150" fill="#5f5f63"/>
    <polygon points="139,150 183,75 225,150" fill="#8b8b8f"/>
  </svg>
  <p class="who__caption fine">We guide students from first enquiry to arrival, matching each learner with the right university, course and city for their goals.</p>
</section>

<!-- What we do -->
<section class="slide slide--what">
  <div class="header-band" style="width:324px;">WHAT WE DO</div>
  <div class="brand brand--corner"><span class="brand__square"></span>KORVAPATH</div>

  <div class="what__icon" style="left:30px;">
    <svg width="24" height="24" viewBox="0 0 24 24" aria-hidden="true" fill="none" stroke="#fff" stroke-width="1.6">
      <circle cx="14" cy="10" r="6"/><line x1="9.5" y1="14.5" x2="4" y2="20"/>
    </svg>
  </div>
  <div class="what__icon" style="left:180px;">
    <svg width="24" height="24" viewBox="0 0 24 24" aria-hidden="true" fill="none" stroke="#fff" stroke-width="1.5">
      <path d="M16 7.5c-1-1.3-2.5-1.8-4-1.8-2.2 0-3.7 1.1-3.7 2.8 0 3.8 7.6 2 7.6 6.2 0 1.8-1.6 3-3.9 3-1.7 0-3.3-.7-4.2-2"/>
      <line x1="12" y1="3" x2="12" y2="21"/>
    </svg>
  </div>
  <div class="what__icon" style="left:318px;">
    <svg width="24" height="24" viewBox="0 0 24 24" aria-hidden="true" fill="#fff">
      <rect x="5" y="12" width="3" height="6"/><rect x="10.5" y="7" width="3" height="11"/><rect x="16" y="14" width="3" height="4"/>
    </svg>
  </div>

  <div class="what__label" style="left:0;">SAMPLE TITLE</div>
  <div class="what__label" style="left:138px;">SAMPLE TITLE</div>
  <div class="what__label" style="left:276px;">SAMPLE TITLE</div>

  <div class="what__panel" style="left:0;"><p class="fine">Search programmes and compare universities across many countries.</p></div>
  <div class="what__panel what__panel--mid" style="left:138px;"><p class="fine">Clear fee plans, scholarship advice and budget support for families planning ahead.</p></div>
  <div class="what__panel" style="left:276px;"><p class="fine">Track every application step with regular progress reports.</p></div>
</section>

<!-- Education levels -->
<section class="slide slide--levels">
  <h2 class="slide-title" style="left:24px; top:16px;">EDUCATION LEVELS</h2>
  <div class="brand brand--corner"><span class="brand__square"></span>KORVAPATH</div>
  <div class="levels__photo" role="img" aria-label="Round photo of students at different education levels">
    <span class="levels__photo-label">PHOTO</span>
  </div>
  <div class="levels__heading">TEXT TITLE</div>
  <p class="levels__text fine">We support learners at every stage, from foundation and diploma courses to bachelor, master and doctoral study. Our advisers explain entry needs, timelines and costs so each student can choose with confidence.</p>
  <div class="site-url" style="top:250px;">www.korvapath.ae</div>
  <div class="foot-bar"></div>
</section>

<!-- Why choose -->
<section class="slide slide--why">
  <h2 class="slide-title" style="left:29px; top:20px;">WHY CHOOSE KORVAPATH</h2>
  <div class="brand brand--corner"><span class="brand__square"></span>KORVAPATH</div>
  <svg class="why__donut" width="110" height="110" viewBox="0 0 110 110" aria-hidden="true">
    <defs>
      <linearGradient id="donut-core" x1="0" y1="0" x2="1" y2="1">
        <stop offset="0" stop-color="#cfeef0"/><stop offset="1" stop-color="#d8dde2"/>
      </linearGradient>
    </defs>
    <circle cx="55" cy="55" r="45" fill="none" stroke="#efeff0" stroke-width="10"/>
    <path d="M55 10 A45 45 0 0 1 73 96" fill="none" stroke="#0a1d9a" stroke-width="10"/>
    <circle cx="55" cy="55" r="27" fill="url(#donut-core)"/>
    <circle cx="86" cy="24" r="1.2" fill="#fff"/>
    <circle cx="86" cy="86" r="1.2" fill="#fff"/>
    <circle cx="17" cy="78" r="1.2" fill="#d0d0d3"/>
  </svg>
  <p class="why__point fine" style="left:150px; top:80px;">Trusted advisers with years of experience</p>
  <p class="why__point fine" style="left:150px; top:175px;">Offers from leading universities</p>
  <p class="why__point why__point--plain fine" style="left:38px; top:202px;">Visa and travel help</p>
  <div class="why__rule"></div>
  <p class="why__text fine">Our team knows the admission rules of each country we serve. We prepare strong applications, check every document and stay in touch until the student settles in, so families always know what happens next.</p>
  <div class="site-url" style="top:254px; left:33px;">www.korvapath.ae</div>
  <div class="foot-bar"></div>
</section>

<!-- Study destination -->
<section class="slide slide--destination">
  <div class="header-band" style="width:316px;">STUDY DESTINATION</div>
  <div class="brand brand--corner"><span class="brand__square"></span>KORVAPATH</div>
  <div class="dest__photo" role="img" aria-label="Photo of a group of happy students outdoors under a blue sky"></div>

  <div class="dest__tab" style="left:0;">
    <svg width="16" height="16" viewBox="0 0 16 16" aria-hidden="true" fill="none" stroke="#fff" stroke-width="1.2">
      <circle cx="8" cy="5" r="3"/><path d="M2 15c0-3.5 2.7-5.5 6-5.5s6 2 6 5.5z"/>
    </svg>
  </div>
  <div class="dest__tab dest__tab--light" style="left:103.5px;">
    <svg width="20" height="16" viewBox="0 0 20 16" aria-hidden="true" fill="none" stroke="#fff" stroke-width="1.2">
      <polyline points="1,1 1,15 19,15"/><polyline points="3,12 8,7 11,10 18,3"/>
    </svg>
  </div>
  <div class="dest__tab" style="left:207px;">
    <svg width="14" height="16" viewBox="0 0 14 16" aria-hidden="true" fill="none" stroke="#fff" stroke-width="1.2">
      <circle cx="7" cy="6" r="4.5"/><line x1="5" y1="12.5" x2="9" y2="12.5"/><line x1="5.5" y1="14.5" x2="8.5" y2="14.5"/>
    </svg>
  </div>
  <div class="dest__tab dest__tab--light" style="left:310.5px;">
    <svg width="16" height="16" viewBox="0 0 16 16" aria-hidden="true" fill="none" stroke="#fff" stroke-width="1.2">
      <circle cx="8" cy="8" r="6.5"/><polyline points="9.5,5 6.5,8 9.5,11"/>
    </svg>
  </div>

  <div class="dest__strip"></div>
  <p class="dest__col fine" style="left:18px;">Personal advice shaped around each student.</p>
  <p class="dest__col fine" style="left:122px;">Strong growth in offers every single year.</p>
  <p class="dest__col fine" style="left:225px;">Fresh ideas for choosing the right course.</p>
  <p class="dest__col fine" style="left:329px;">Fast replies and clear deadlines to follow.</p>
</section>

</body>
</html>
```